birchwell hollow cattle company website

we would like a home page, an about us page, a page for sires, a page for dams, A sale page where we can list progreny for sale and a contact us. on the about us page we would like there to be a family picture. on the sires page we would like to have a picture of each sire, a description beside them and a link to their online profile at northern hereford registry. on the dam page we would like to have a picture of each dam, aswell as a description beside them aswell as a link to the northern hereford registry site. would like the website to very mobile phone friendly as expecting most traffic to be on phone. we would like the website to look and feel very mich like a farm, rustic, barbed wire and other farm feels. we would also like a frozen genetics pages where we can include pictures and descriptions of the sires and dams aswell as a price for embryos and semen. we need to website to be easy to maintain so we can update pictures and information as it changes, we would like there to be a feature so that people can sign up to be on our mailing list by giving us their mailing addess and email and full name
aswell as an area where they can send us a message to contact us.

leaving for work for 3 weeks in the canadian arctic will have limited ability to use the internet

Target Market(s)

other ranchers, farmers, cattlemen,

Industry/Entity Type

farming, agriculture, cattle

Coding

Coded - Design and coding required

Requirements
Must have
• about page, contact page, sires page, dams page, SALE page.
Nice to have
• country/farm vibe, barbed wire, wood,

```html
<!DOCTYPE html>
<html lang="en">
<head>
<meta charset="utf-8">
<title>Birchwell Hollow Cattle Company</title>
<link href="https://fonts.googleapis.com/css2?family=Lexend:wght@400;600;700&family=Outfit:wght@300;400;500&display=swap" rel="stylesheet">
<style>
:root{
  --gold:#d9a032;
  --gold-dark:#b9821f;
  --cream:#f6ecd5;
  --ink:#1f1c18;
  --text:#4a443d;
  --white:#ffffff;
  --footer:#1c1c1c;
  --hero-top:#5b4a3a;
  --hero-mid:#a8682c;
  --hero-bot:#2a1f17;
}
*{box-sizing:border-box;margin:0;padding:0}
html,body{width:1200px;height:4658px;overflow:hidden}
body{position:relative;background:var(--white);font-family:"Outfit",sans-serif;color:var(--text)}
.abs{position:absolute}
h1,h2,h3{font-family:"Lexend",sans-serif;font-weight:700;color:var(--ink);text-transform:uppercase}
.btn{position:absolute;display:flex;align-items:center;justify-content:center;border-radius:30px;font-family:"Outfit",sans-serif;font-size:13px;font-weight:500;text-decoration:none}
.btn-gold{background:var(--gold);color:var(--white)}
.btn-white{background:var(--white);color:var(--ink)}

/* header */
.site-header{position:absolute;left:0;top:0;width:1200px;height:90px;z-index:5}
.brand{position:absolute;left:112px;top:24px;display:flex;align-items:center;gap:8px;font-family:"Lexend",sans-serif;font-weight:700;color:var(--white);font-size:13px;line-height:1.1;text-transform:uppercase;width:130px}
.brand-dot{width:14px;height:14px;border-radius:50%;background:var(--white);flex:none}
.main-nav{position:absolute;left:349px;top:34px;display:flex;gap:0;font-size:12px;color:var(--white);font-weight:500}
.main-nav span{padding:0 11px;border-left:1px solid rgba(255,255,255,.7);line-height:12px}
.main-nav span:first-child{border-left:none;padding-left:0}
.header-line{position:absolute;left:112px;top:82px;width:976px;height:1px;background:rgba(255,255,255,.35)}
.login{position:absolute;left:1015px;top:35px;font-size:12px;color:var(--white);font-weight:500}
.cart{position:absolute;left:1053px;top:28px}

/* hero */
.hero{position:absolute;left:0;top:0;width:1200px;height:740px;background:linear-gradient(180deg,var(--hero-top) 0%,#7a5433 30%,var(--hero-mid) 48%,#4a3322 65%,var(--hero-bot) 100%)}
.hero h1{position:absolute;left:112px;top:172px;font-size:72px;line-height:74px;color:var(--white);letter-spacing:1px}

/* focus */
.focus{position:absolute;left:0;top:720px;width:1200px;height:590px;background:var(--cream)}
.focus h2{position:absolute;left:0;top:92px;width:1200px;text-align:center;font-size:38px;line-height:45px;font-weight:600}
.card{position:absolute;width:273px;background:var(--white);border-radius:14px;box-shadow:0 6px 18px rgba(0,0,0,.08)}
.card .photo{position:absolute;left:6px;top:6px;width:261px;height:173px;border-radius:10px}
.card .icon{position:absolute;left:106px;top:150px;width:60px;height:60px;border-radius:50%;background:var(--gold);display:flex;align-items:center;justify-content:center;border:3px solid var(--white)}
.card h3{position:absolute;left:0;width:273px;text-align:center;font-size:15px;line-height:20px;font-weight:600}
.card p{position:absolute;left:24px;width:225px;text-align:center;font-size:12px;line-height:19px}
.edge{position:absolute;left:0;width:1200px}

/* about */
.about-photo{position:absolute;left:136px;top:1400px;width:428px;height:428px;border-radius:50%;border:5px solid var(--gold);background:linear-gradient(160deg,#6d4e34,#8d6a4a 45%,#3b3029)}
.play{position:absolute;left:466px;top:1707px;width:80px;height:80px;border-radius:50%;background:#1a1a1a;display:flex;align-items:center;justify-content:center}
.about-copy{position:absolute;left:611px;top:1470px;width:460px}
.about-copy h2{font-size:39px;line-height:45px;font-weight:600;margin-bottom:12px}
.body-text{font-size:12.5px;line-height:19px;color:var(--text)}
.body-text+.body-text{margin-top:12px}

/* sale */
.centered-title{position:absolute;left:0;width:1200px;text-align:center;font-size:38px;font-weight:600}
.sale-sub{position:absolute;left:350px;top:1969px;width:500px;text-align:center;font-size:12.5px;line-height:19px}
.sale-photo{position:absolute;left:112px;top:2038px;width:976px;height:465px;border-radius:28px;background:linear-gradient(180deg,#8fa1ac 0%,#7b6c5c 40%,#6b3a20 62%,#b69864 100%)}

/* frozen */
.frozen-copy{position:absolute;left:143px;top:2740px;width:440px}
.frozen-copy h2{font-size:39px;line-height:45px;font-weight:600;margin-bottom:14px}
.frozen-photo{position:absolute;left:627px;top:2674px;width:430px;height:430px;border-radius:50%;border:5px solid var(--gold);background:linear-gradient(170deg,#5b4b3a 0%,#8a7150 40%,#c9a86a 75%,#a98b55 100%)}

/* newsletter */
.newsletter{position:absolute;left:0;top:3740px;width:1200px;height:450px;background:linear-gradient(180deg,#e9e8dc 0%,#a9b59a 28%,#6c7c4f 50%,#8d8a5e 70%,#b58a5a 100%)}
.field{position:absolute;top:3911px;height:42px;border-radius:24px;background:var(--white);font-size:12px;color:#8a857e;padding-left:22px;display:flex;align-items:center}

/* footer */
.site-footer{position:absolute;left:0;top:4183px;width:1200px;height:475px;background:var(--footer)}
.footer-brand{position:absolute;left:0;top:4290px;width:1200px;display:flex;justify-content:center;align-items:center;gap:12px;font-family:"Lexend",sans-serif;font-weight:700;font-size:28px;color:var(--white);text-transform:uppercase}
.footer-brand .brand-dot{width:20px;height:20px}
.footer-nav{position:absolute;left:0;top:4435px;width:1200px;display:flex;justify-content:center;font-size:14px;color:var(--white)}
.footer-nav span{padding:0 30px;border-left:1px solid rgba(255,255,255,.6);line-height:13px}
.footer-nav span:first-child{border-left:none}
.social{position:absolute;top:4489px;width:38px;height:38px;border-radius:50%;background:#3a3a3a}
.footer-line{position:absolute;left:112px;top:4592px;width:976px;height:1px;background:#3e3e3e}
.copyright{position:absolute;left:0;top:4614px;width:1200px;text-align:center;font-size:11.5px;color:#d8d8d8}
</style>
</head>
<body>

<section class="hero" role="img" aria-label="Herd of black cattle walking across a pasture at sunset with trees behind"></section>

<header class="site-header">
  <div class="brand"><span class="brand-dot"></span>Birchwell Hollow</div>
  <nav class="main-nav">
    <span>Home</span><span>About</span><span>Sires</span><span>Dams</span><span>Sale</span><span>Frozen Genetics</span><span>Contact</span>
  </nav>
  <div class="login">Login</div>
  <svg class="cart" width="30" height="30" viewBox="0 0 30 30"><rect x="4" y="8" width="20" height="18" rx="3" fill="none" stroke="#fff" stroke-width="2"/><path d="M9 8V6a5 5 0 0 1 10 0v2" fill="none" stroke="#fff" stroke-width="2"/><path d="M9 15l3 3 6-6" fill="none" stroke="#fff" stroke-width="2"/><circle cx="24" cy="6" r="5" fill="#e0352b"/></svg>
  <div class="header-line"></div>
</header>

<div class="abs" style="left:0;top:0;width:1200px">
  <h1 class="hero-title" style="position:absolute;left:112px;top:172px;font-size:72px;line-height:74px;color:#fff;font-family:'Lexend',sans-serif;font-weight:700;letter-spacing:1px">BUILT ON ANGUS<br>EXCELLENCE</h1>
</div>
<a class="btn btn-gold" style="left:114px;top:335px;width:133px;height:42px">View Our Sires</a>
<a class="btn btn-white" style="left:255px;top:335px;width:133px;height:42px">Cattle For Sale</a>

<section class="focus">
  <h2>Focused On<br>What Matters Most</h2>
</section>
<svg class="edge" style="top:700px" height="50" viewBox="0 0 1200 50" preserveAspectRatio="none"><path d="M0 30 L40 22 L70 34 L110 18 L150 30 L190 20 L230 32 L270 16 L320 30 L360 22 L400 34 L450 20 L500 30 L540 18 L590 32 L640 22 L690 34 L740 18 L790 30 L840 20 L890 32 L940 16 L990 30 L1040 22 L1090 34 L1140 18 L1200 28 L1200 50 L0 50Z" fill="#f6ecd5"/></svg>

<article class="card" style="left:168px;top:922px;height:292px">
  <div class="photo" role="img" aria-label="Two ranchers walking through a barn with cattle feeding" style="background:linear-gradient(160deg,#6c5a48,#4a4038 60%,#2f2a25)"></div>
  <div class="icon"><svg width="28" height="28" viewBox="0 0 28 28"><path d="M6 15c3-1 5-1 8 1l5-4 3 3-7 7H8z" fill="#fff"/><circle cx="17" cy="8" r="3" fill="#fff"/></svg></div>
  <h3 style="top:222px">Functional<br>Real-World Cattle</h3>
</article>
<article class="card" style="left:464px;top:922px;height:292px">
  <div class="photo" role="img" aria-label="Veterinarian checking dairy cows in a feeding barn" style="background:linear-gradient(160deg,#7f8c99,#40424a 55%,#2b2b30)"></div>
  <div class="icon"><svg width="30" height="30" viewBox="0 0 30 30"><circle cx="15" cy="15" r="10" fill="none" stroke="#fff" stroke-width="2.5"/><path d="M10 15l4 4 7-8" fill="none" stroke="#fff" stroke-width="2.5"/></svg></div>
  <h3 style="top:222px">Proven<br>Bloodlines</h3>
</article>
<article class="card" style="left:759px;top:922px;height:292px">
  <div class="photo" role="img" aria-label="Farm family standing with black and white cattle on green pasture" style="background:linear-gradient(180deg,#9aaeb7,#5e6f49 50%,#3f5a2c)"></div>
  <div class="icon"><svg width="28" height="28" viewBox="0 0 28 28"><path d="M14 24S4 17 4 10a5 5 0 0 1 10-2 5 5 0 0 1 10 2c0 7-10 14-10 14z" fill="#fff"/></svg></div>
  <h3 style="top:222px">Honest,<br>Straightforward</h3>
</article>

<svg class="edge" style="top:1285px" height="40" viewBox="0 0 1200 40" preserveAspectRatio="none"><path d="M0 0 L1200 0 L1200 18 L1150 28 L1100 14 L1050 26 L1000 12 L950 28 L900 16 L850 30 L800 14 L750 26 L700 12 L650 28 L600 16 L550 30 L500 14 L450 26 L400 12 L350 28 L300 16 L250 30 L200 14 L150 26 L100 12 L50 28 L0 16Z" fill="#f6ecd5"/></svg>

<div class="about-photo" role="img" aria-label="Family of four standing in front of a wooden barn holding a puppy"></div>
<div class="play"><svg width="24" height="24" viewBox="0 0 24 24"><path d="M7 4l13 8-13 8z" fill="#d9a032"/></svg></div>
<div class="about-copy">
  <h2>Built on Family,<br>Tradition, &amp; Strong<br>Genetics</h2>
  <p class="body-text">We are a family-run cattle operation dedicated to producing high-quality Angus genetics for commercial and purebred breeders.</p>
  <p class="body-text">Our program focuses on structure, temperament, performance, and maternal strength — ensuring cattle that work in real ranch conditions.</p>
  <p class="body-text">Every animal we raise reflects our commitment to honest breeding careful selection, and long-term herd improvement.</p>
</div>

<h2 class="centered-title" style="top:1910px">Quality Cattle Available</h2>
<p class="sale-sub">We offer select progeny throughout the year, including bulls, heifers, and replacement females bred for performance and longevity.</p>
<div class="sale-photo" role="img" aria-label="Red bull standing on straw in front of steel pen gates"></div>
<a class="btn btn-gold" style="left:520px;top:2535px;width:160px;height:42px">View Sale Listings</a>

<div class="frozen-copy">
  <h2>Frozen Genetics<br>Available</h2>
  <p class="body-text">Embryos and semen from our proven sires and elite donor dams are available in limited quantities. Each mating is carefully planned with performance, structural soundness, maternal strength, and long-term profitability in mind.</p>
  <p class="body-text">Our frozen genetics program allows breeders to access top-tier bloodlines without compromise. Whether you're looking to strengthen maternal traits, improve carcass merit, increase growth performance, or add proven pedigree power to your herd, our genetics are designed to move your program forward with confidence.</p>
</div>
<a class="btn btn-gold" style="left:142px;top:3014px;width:192px;height:42px">Explore Frozen Genetics</a>
<div class="frozen-photo" role="img" aria-label="Black and white calf resting on straw in a barn"></div>

<h2 class="centered-title" style="top:3192px">Meet Our Herd Sires</h2>
<article class="card" style="left:168px;top:3271px;height:307px">
  <div class="photo" role="img" aria-label="Breeder in a white coat holding a sample inside a dairy barn" style="background:linear-gradient(160deg,#7b838c,#4a4c50 55%,#2d2d30)"></div>
  <h3 style="top:196px">Proven Performance<br>Genetics</h3>
  <p style="top:242px">Selected for growth, carcass merit, &amp; overall herd improvement.</p>
</article>
<article class="card" style="left:464px;top:3271px;height:307px">
  <div class="photo" role="img" aria-label="Brown cow with her calf standing in tall grass" style="background:linear-gradient(160deg,#5f7a3c,#8a5a36 55%,#4d5f2c)"></div>
  <h3 style="top:196px">Maternal Strength<br>Influence</h3>
  <p style="top:242px">Passing on strong maternal traits that build productive, efficient.</p>
</article>
<article class="card" style="left:759px;top:3271px;height:307px">
  <div class="photo" role="img" aria-label="Rancher kneeling beside black and white cattle on pasture" style="background:linear-gradient(180deg,#a3b2b8,#5d6a45 50%,#3e4f2b)"></div>
  <h3 style="top:196px">Calm &amp; Workable<br>Disposition</h3>
  <p style="top:242px">Easy-handling cattle that fit real working environments.</p>
</article>
<a class="btn btn-gold" style="left:533px;top:3614px;width:134px;height:42px">View All Sires</a>

<section class="newsletter" role="img" aria-label="Hereford cattle resting on a grassy meadow with trees behind"></section>
<svg class="edge" style="top:3728px" height="40" viewBox="0 0 1200 40" preserveAspectRatio="none"><path d="M0 0 L1200 0 L1200 22 L1140 30 L1090 16 L1040 28 L980 14 L920 30 L860 18 L800 32 L740 14 L680 28 L620 16 L560 30 L500 14 L440 28 L380 16 L320 32 L260 14 L200 28 L140 16 L80 30 L0 18Z" fill="#ffffff"/></svg>
<h2 class="centered-title" style="top:3845px">Stay Updated</h2>
<div class="field" style="left:157px;width:241px">Full Name</div>
<div class="field" style="left:405px;width:240px">Email Address</div>
<div class="field" style="left:652px;width:241px">Mailing Address</div>
<a class="btn btn-gold" style="left:904px;top:3911px;width:137px;height:42px">Subscribe Now</a>

<footer class="site-footer"></footer>
<svg class="edge" style="top:4160px" height="40" viewBox="0 0 1200 40" preserveAspectRatio="none"><path d="M0 24 L60 14 L120 28 L180 12 L240 26 L300 16 L360 30 L420 14 L480 26 L540 12 L600 28 L660 16 L720 30 L780 12 L840 26 L900 14 L960 28 L1020 16 L1080 30 L1140 14 L1200 24 L1200 40 L0 40Z" fill="#1c1c1c"/></svg>
<div class="footer-brand"><span class="brand-dot"></span>Birchwell Hollow</div>
<nav class="footer-nav"><span>Home</span><span>About Us</span><span>Sires</span><span>Dams</span><span>Sale</span><span>Frozen Genetics</span><span>Contact Us</span></nav>
<span class="social" style="left:510px;background:var(--gold)"></span>
<span class="social" style="left:557px"></span>
<span class="social" style="left:604px"></span>
<span class="social" style="left:651px"></span>
<div class="footer-line"></div>
<p class="copyright">©Copyright 2026 Birchwell Hollow. All Rights Reserved.</p>

</body>
</html>
```